BrivoTerna. Lantern of the Steady Harvest. Business card

Professional business card for BrivoTerna (Lantern of the Steady Harvest)
My rationale: Strategy-> Execution-> Results-> Value that lead to the BrivoTerna name: We put the Lantern of the Steady Harvest.
We deliver value to our customers helping them at defining a good strategy (cyan arrow). 90% of well formulated strategies fail due to poor execution so we also consider strategical execution very important (green arrow). Due to the execution we obtain the results (blue arrow). Finally, the results provide feedback to redefine strategy, and the new strategy has to be executed and new results obtained providing new feedback and on and on. It's like a wheel that finally, must create corporate value: value for shareholders, staholders, employees, providers...-

Target Market(s)

CEOs and steering comitees , invewrnent funds

Industry/Entity Type

Business Consultant

Contact Information for Business Card

Teodoro Vinsquel
CEO & Founder
teodoro.vinsquel@brivoterna-example.com
Mobile: +34 655.803.912
www.brivoterna-example.com

Colors

Designer to choose colors to be used in the design.

Requirements
Nice to have
• Nice to hace the words: Strategy, execution, results
• Nice to vave the claim: Lantern of the Steady Harvest
• The three colors should be shown:
• cyan for STRATEGY
• green for EXECUTION
• blue for RESULTS
Should not have
• Complete black background

```html
<!DOCTYPE html>
<html lang="en">
<head>
<meta charset="utf-8">
<title>BrivoTerna — Business Card</title>
<link href="https://fonts.googleapis.com/css2?family=Roboto+Condensed:wght@400;500;700&display=swap" rel="stylesheet">
<style>
  :root {
    --backdrop: #ecebe8;
    --paper: #ffffff;
    --navy: #213a8f;
    --cyan: #29a9e0;
    --green: #8dc63f;
    --ink: #333333;
    --white: #ffffff;
  }
  * { box-sizing: border-box; margin: 0; padding: 0; }
  html, body {
    width: 1200px; height: 900px; overflow: hidden;
    background: var(--backdrop);
    font-family: "Roboto Condensed", Arial, sans-serif;
  }
  .card {
    position: absolute; left: 311px; width: 577px; height: 329px;
    background: var(--paper); overflow: hidden;
    box-shadow: 0 6px 16px rgba(0,0,0,.18);
  }
  .card--front { top: 98px; }
  .card--back { top: 472px; }

  .front__mark {
    position: absolute; left: 248px; top: 66px;
    width: 82px; height: 82px; border-radius: 50%;
    background: var(--navy);
  }
  .front__name {
    position: absolute; left: 0; right: 0; top: 168px;
    text-align: center; font-weight: 700; font-size: 54px; line-height: 1.1;
    color: var(--navy); letter-spacing: -0.5px;
  }
  .front__claim {
    position: absolute; left: 0; right: 0; top: 224px;
    text-align: center; font-weight: 500; font-size: 18px;
    color: var(--ink); letter-spacing: 0.6px; text-transform: uppercase;
  }
  .pillars { position: absolute; left: 0; right: 0; bottom: 0; height: 46px; display: flex; }
  .pillar {
    display: flex; align-items: center; justify-content: center;
    color: var(--white); font-size: 18px; font-weight: 500;
    letter-spacing: 0.4px; text-transform: uppercase;
  }
  .pillar--strategy { width: 185px; background: var(--cyan); }
  .pillar--execution { width: 207px; background: var(--green); }
  .pillar--results { width: 185px; background: var(--navy); }

  .back__name {
    position: absolute; left: 32px; top: 26px;
    font-weight: 700; font-size: 40px; color: var(--navy); letter-spacing: -0.5px;
  }
  .holder { position: absolute; right: 31px; top: 32px; text-align: right; }
  .holder__name { font-weight: 700; font-size: 17px; color: var(--navy); letter-spacing: 0.5px; text-transform: uppercase; }
  .holder__role { font-size: 12px; color: var(--ink); letter-spacing: 0.3px; text-transform: uppercase; }

  .wave { position: absolute; left: 0; top: 0; width: 577px; height: 329px; }
  .wave__base { fill: var(--navy); }
  .wave__swoosh { fill: var(--green); }
  .wave__band { fill: var(--cyan); }
  .wave__disc { fill: var(--paper); }
  .wave__mark { fill: var(--navy); }

  .contacts { position: absolute; left: 31px; top: 225px; list-style: none; }
  .contacts__item {
    display: flex; align-items: center; height: 24px;
    color: var(--white); font-size: 15.5px;
  }
  .contacts__icon { width: 17px; height: 17px; margin-right: 7px; fill: none; stroke: var(--white); stroke-width: 1.6; }
</style>
</head>
<body>

<section class="card card--front">
  <div class="front__mark" aria-hidden="true"></div>
  <h1 class="front__name">BrivoTerna</h1>
  <p class="front__claim">Lantern of the Steady Harvest</p>
  <div class="pillars">
    <div class="pillar pillar--strategy">Strategy</div>
    <div class="pillar pillar--execution">Execution</div>
    <div class="pillar pillar--results">Results</div>
  </div>
</section>

<section class="card card--back">
  <svg class="wave" viewBox="0 0 577 329" aria-hidden="true">
    <path class="wave__base" d="M0 180 Q200 182 360 196 Q470 206 577 222 L577 329 L0 329 Z"/>
    <path class="wave__swoosh" d="M194 166 Q270 172 345 180 L345 186 Q270 178 194 168 Z"/>
    <path class="wave__band" d="M430 184 Q510 190 577 198 L577 214 Q510 206 430 200 Z"/>
    <circle class="wave__disc" cx="404" cy="218" r="78"/>
    <circle class="wave__mark" cx="404" cy="214" r="50"/>
  </svg>

  <div class="back__name">BrivoTerna</div>
  <div class="holder">
    <div class="holder__name">Teodoro Vinsquel</div>
    <div class="holder__role">CEO &amp; Founder</div>
  </div>

  <ul class="contacts">
    <li class="contacts__item">
      <svg class="contacts__icon" viewBox="0 0 18 18"><rect x="5" y="1.5" width="8" height="15" rx="1.5"/><line x1="8" y1="14" x2="10" y2="14"/></svg>
      +34 655.803.912
    </li>
    <li class="contacts__item">
      <svg class="contacts__icon" viewBox="0 0 18 18"><rect x="1.5" y="4" width="15" height="10"/><path d="M1.5 4 L9 10 L16.5 4"/></svg>
      teodoro.vinsquel@brivoterna-example.com
    </li>
    <li class="contacts__item">
      <svg class="contacts__icon" viewBox="0 0 18 18"><circle cx="9" cy="9" r="7.5"/><ellipse cx="9" cy="9" rx="3.2" ry="7.5"/><line x1="1.5" y1="9" x2="16.5" y2="9"/></svg>
      www.brivoterna-example.com
    </li>
  </ul>
</section>

</body>
</html>
```